Landing Page and Logo for Auto-Blogging Platform

I created a platform that allows users to start a blog for their business, hobby, charity, etc. I need a landing page where users can learn about the platform, benefits of consistent blogging, SEO value, plans/pricing, etc. The landing page needs to have multiple call to action buttons encouraging the visitor to register/sign up for a free trial.

In addition to the landing page, I need a page for users to establish the settings for their blog. This page should be a fairly simple form, intended for the user to enter a few details to set up their blog:
1. Name of Blog
2. Up to 10 topics and/or keywords the blog should focus on
3. Theme: Color-scheme and logo upload for blog.

I have attached the specifications of the platform's functionality so you can better understand how it works, plans/pricing, etc.

I also need a logo for the business. The name of the platform is PostNook.

Target Market(s)

Website owners, bloggers, business owners

Industry/Entity Type

Technology, Internet, web design

Coding

Coded - Design and coding required

Number of Pages Required

2 page

Colors
0054AA
0677BA
7BADD7
CADEEF
E8F1F8
0094D4
00A9DD
6FCCEA
C7EBF8
E9F6FB

Requirements
Must have
• Eye-catching design but fairly light on content (keep it simple and brief.)
Nice to have
• Eye-catching yet simple design, clean and easy to understand what we are offering.
Should not have
• Too much “wordy” and confusing content.

```html
<!DOCTYPE html>
<html lang="en">
<head>
<meta charset="UTF-8">
<title>PostNook – Start Your Blog</title>
<link href="https://fonts.googleapis.com/css2?family=Poppins:wght@400;500;600;700&display=swap" rel="stylesheet">
<style>
:root{
  --navy:#0b3a94;
  --deep:#0a2f80;
  --blue:#0054aa;
  --mid:#0677ba;
  --sky:#00a9dd;
  --aqua:#6fccea;
  --pale:#e9f6fb;
  --yellow:#f7c51e;
  --white:#ffffff;
  --ink:#0b2a66;
}
*{box-sizing:border-box;margin:0;padding:0}
html,body{width:703px;height:1200px;overflow:hidden;background:var(--white);font-family:'Poppins',sans-serif}
.canvas{position:relative;width:703px;height:1200px}
.brand-top{position:absolute;top:22px;left:0;width:100%;display:flex;justify-content:center;align-items:center;gap:10px;color:var(--blue);font-weight:700;font-size:32px}
.brand-mark{width:30px;height:30px;border-radius:50%;background:var(--blue)}
.page{position:absolute;left:33px;top:95px;width:637px;height:1085px;background:linear-gradient(180deg,var(--navy),#0c47b0 60%,var(--deep));overflow:hidden}
.nav{position:absolute;top:20px;left:24px;right:24px;height:32px;display:flex;align-items:center}
.nav-brand{display:flex;align-items:center;gap:7px;color:var(--white);font-weight:700;font-size:19px}
.nav-brand .brand-mark{width:20px;height:20px;background:var(--white)}
.nav-links{display:flex;gap:22px;margin-left:auto;margin-right:28px;font-size:11px;color:var(--white)}
.nav-links .active{font-weight:700}
.signup{background:var(--yellow);color:var(--ink);font-size:11px;font-weight:500;padding:5px 18px;border-radius:14px}
.card{position:absolute;left:22px;width:595px;border-radius:4px;background:linear-gradient(100deg,#7fd6ee 0%,#2aa6de 45%,#1763c9 100%);color:var(--white)}
.hero{top:65px;height:305px}
.setup{top:393px;height:282px}
.tag{display:inline-block;background:var(--white);color:var(--ink);font-size:10px;font-weight:500;padding:3px 9px;border-radius:3px}
.hero-copy{position:absolute;left:22px;top:24px;width:270px}
h1{font-size:21px;line-height:1.22;font-weight:700;margin:12px 0 10px}
h2{font-size:19px;line-height:1.25;font-weight:700;margin:12px 0 10px}
p.lead{font-size:11px;line-height:1.5;opacity:.95}
.cta{display:inline-flex;align-items:center;gap:12px;margin-top:16px;background:var(--white);color:var(--ink);font-size:12px;font-weight:500;padding:4px 4px 4px 18px;border-radius:20px}
.cta .dot{width:24px;height:24px;border-radius:50%;background:var(--yellow);display:flex;align-items:center;justify-content:center}
.hero-photo{position:absolute;right:10px;top:8px;width:290px;height:290px}
.setup-copy{position:absolute;left:22px;top:22px;width:270px}
.form{position:absolute;left:305px;top:26px;width:265px}
.field label{display:block;font-size:10.5px;font-weight:600;margin-bottom:5px}
.field .input{background:var(--white);border-radius:3px;height:24px;margin-bottom:14px}
.field .input.tall{height:50px}
.upload{display:flex;align-items:center;justify-content:center}
.plans{position:absolute;top:705px;left:10px;right:10px;display:flex;gap:6px}
.plan{position:relative;flex:1;height:330px;border-radius:3px;padding:30px 18px 0;background:linear-gradient(160deg,#7fd6ee 0%,#2aa6de 50%,#1763c9 100%);color:var(--white)}
.plan.featured{background:linear-gradient(160deg,#5ec7ec 0%,#1f8fd6 50%,#1557c0 100%);border:1px solid rgba(255,255,255,.6)}
.plan h3{font-size:17px;font-weight:700}
.price{font-size:27px;font-weight:600;margin:8px 0 10px}
.per{font-size:9.5px}
.per b{font-weight:700}
.plan hr{border:0;border-top:1px solid rgba(255,255,255,.6);margin:16px 0 18px}
.plan ul{list-style:none;font-size:10.5px}
.plan li{display:flex;gap:8px;align-items:center;margin-bottom:10px}
.badge{position:absolute;top:12px;right:12px;background:var(--yellow);color:var(--ink);font-size:9px;font-weight:600;padding:3px 7px;border-radius:3px}
.plan .cta{position:absolute;bottom:18px;left:18px;font-size:10.5px;margin:0;padding:3px 3px 3px 14px}
</style>
</head>
<body>
<div class="canvas">
  <div class="brand-top"><span class="brand-mark"></span>PostNook</div>

  <div class="page">
    <nav class="nav">
      <div class="nav-brand"><span class="brand-mark"></span>PostNook</div>
      <div class="nav-links"><span>Home</span><span>Services</span><span>Pricing</span><span class="active">Set Up</span><span>About</span></div>
      <span class="signup">Sign up</span>
    </nav>

    <section class="card hero">
      <div class="hero-copy">
        <span class="tag">#StartYourBlog</span>
        <h1>Start Your Blog with Ease: Empower Your Passion, Business, or Cause</h1>
        <p class="lead">Create a blog in minutes. Perfect for businesses, hobbies, or charities. Share your story and connect with your audience effortlessly. Get started today!</p>
        <span class="cta">Start free trial <span class="dot"><svg width="10" height="10" viewBox="0 0 10 10"><path d="M1 5h7M5 2l3 3-3 3" stroke="#0b2a66" stroke-width="1.5" fill="none"/></svg></span></span>
      </div>
      <svg class="hero-photo" viewBox="0 0 290 290" role="img" aria-label="Photo of hands typing on a laptop beside a coffee cup">
        <defs><linearGradient id="ph" x1="0" y1="0" x2="1" y2="1"><stop offset="0" stop-color="#e7eef4"/><stop offset=".6" stop-color="#b9c6d2"/><stop offset="1" stop-color="#6d7f92"/></linearGradient></defs>
        <polygon points="145,0 270,72 270,218 145,290 20,218 20,72" fill="url(#ph)"/>
      </svg>
    </section>

    <section class="card setup">
      <div class="setup-copy">
        <span class="tag">#StartYourBlog</span>
        <h2>Set Up Your Blog: Customize and Personalize</h2>
        <p class="lead">Get your blog ready in just a few steps. Fill out the form below to name your blog, choose focus topics, and customize your theme. With these simple settings, you'll be on your way to creating a blog that truly represents you and your brand.</p>
      </div>
      <div class="form">
        <div class="field"><label>Blog Name</label><div class="input"></div></div>
        <div class="field"><label>Focus Topics &amp; Keywords</label><div class="input tall"></div></div>
        <div class="field"><label>Theme Customization</label><div class="input"></div></div>
        <div class="field"><label>Upload Your Logo</label><div class="input tall upload" style="height:30px">
          <svg width="18" height="14" viewBox="0 0 18 14"><path d="M5 12H4a3.5 3.5 0 0 1 0-7 5 5 0 0 1 9.5-1A4 4 0 0 1 14 12h-1M9 6v7M6.5 8.5 9 6l2.5 2.5" stroke="#7b9bbd" stroke-width="1.3" fill="none"/></svg>
        </div></div>
      </div>
    </section>

    <div class="plans">
      <article class="plan">
        <h3>Base Plan</h3>
        <div class="price">$9.99/MO</div>
        <div class="per"><b>for every month</b> you will get</div>
        <hr>
        <ul>
          <li><svg width="10" height="10" viewBox="0 0 10 10"><path d="M1 5l3 3 5-6" stroke="#fff" stroke-width="1.4" fill="none"/></svg>1 blog post</li>
          <li><svg width="10" height="10" viewBox="0 0 10 10"><path d="M1 5l3 3 5-6" stroke="#fff" stroke-width="1.4" fill="none"/></svg>Up to 2,000 words</li>
        </ul>
        <span class="cta">SUBSCRIBE NOW <span class="dot"><svg width="10" height="10" viewBox="0 0 10 10"><path d="M1 5h7M5 2l3 3-3 3" stroke="#0b2a66" stroke-width="1.5" fill="none"/></svg></span></span>
      </article>
      <article class="plan featured">
        <span class="badge">#BestDeal</span>
        <h3>Premium Plan</h3>
        <div class="price">$14.99/MO</div>
        <div class="per"><b>for every week</b> you will get</div>
        <hr>
        <ul>
          <li><svg width="10" height="10" viewBox="0 0 10 10"><path d="M1 5l3 3 5-6" stroke="#fff" stroke-width="1.4" fill="none"/></svg>1 blog post</li>
          <li><svg width="10" height="10" viewBox="0 0 10 10"><path d="M1 5l3 3 5-6" stroke="#fff" stroke-width="1.4" fill="none"/></svg>Up to 2,000 words</li>
        </ul>
        <span class="cta">SUBSCRIBE NOW <span class="dot"><svg width="10" height="10" viewBox="0 0 10 10"><path d="M1 5h7M5 2l3 3-3 3" stroke="#0b2a66" stroke-width="1.5" fill="none"/></svg></span></span>
      </article>
      <article class="plan">
        <h3>Ultimate Plan</h3>
        <div class="price">$24.99/MO</div>
        <div class="per"><b>for every day</b> you will get</div>
        <hr>
        <ul>
          <li><svg width="10" height="10" viewBox="0 0 10 10"><path d="M1 5l3 3 5-6" stroke="#fff" stroke-width="1.4" fill="none"/></svg>1 blog post</li>
          <li><svg width="10" height="10" viewBox="0 0 10 10"><path d="M1 5l3 3 5-6" stroke="#fff" stroke-width="1.4" fill="none"/></svg>Up to 3,000 words</li>
          <li><svg width="10" height="10" viewBox="0 0 10 10"><path d="M1 5l3 3 5-6" stroke="#fff" stroke-width="1.4" fill="none"/></svg>Unlimited manual posting</li>
        </ul>
        <span class="cta">SUBSCRIBE NOW <span class="dot"><svg width="10" height="10" viewBox="0 0 10 10"><path d="M1 5h7M5 2l3 3-3 3" stroke="#0b2a66" stroke-width="1.5" fill="none"/></svg></span></span>
      </article>
    </div>
  </div>
</div>
</body>
</html>
```